Specialised investor in e-mobility and energy wants business card design

We need a business card design that fits our existing corporate design. <The look and feel must be 'sharp'/'clean', dynamic, communicate momentum, professionalism etc (as one would imagine from a firm in the financial sector). We like the idea of a reverse-side of the card that includes the logo, and the name and contact details on the other. We expect the deliverable to be whatever format might be required to be able to get cards printed directly by a service such as kelmo press. Our website is www.zub.capital

```html
<!DOCTYPE html>
<html lang="en">
<head>
<meta charset="utf-8">
<title>ZUB Capital Business Card</title>
<link href="https://fonts.googleapis.com/css2?family=Poppins:wght@400;600&display=swap" rel="stylesheet">
<style>
  :root {
    --backdrop: #2c2c2c;
    --card-white: #ffffff;
    --brand-green: #314f22;
    --ink: #1d1d1d;
    --rule: #9a9a9a;
  }
  html, body {
    margin: 0;
    padding: 0;
    overflow: hidden;
  }
  body {
    width: 1093px;
    height: 1200px;
    background: var(--backdrop);
    position: relative;
    font-family: 'Poppins', sans-serif;
  }
  .card {
    position: absolute;
    left: 265px;
    width: 577px;
    height: 356px;
    border-radius: 24px;
    overflow: hidden;
  }
  .card-front {
    top: 226px;
    background: var(--card-white);
  }
  .card-back {
    top: 621px;
    background: var(--brand-green);
  }
  .wordmark {
    position: absolute;
    font-weight: 400;
    white-space: nowrap;
    line-height: 1;
  }
  .card-front .wordmark {
    left: 30px;
    top: 158px;
    font-size: 40px;
    color: var(--brand-green);
  }
  .card-back .wordmark {
    left: 0;
    right: 0;
    top: 146px;
    text-align: center;
    font-size: 60px;
    color: var(--card-white);
  }
  .divider {
    position: absolute;
    left: 289px;
    top: 74px;
    width: 1px;
    height: 209px;
    background: linear-gradient(to bottom, rgba(154,154,154,0), var(--rule) 30%, var(--rule) 70%, rgba(154,154,154,0));
  }
  .details {
    position: absolute;
    left: 311px;
    top: 90px;
    color: var(--ink);
  }
  .person-name {
    margin: 0;
    font-size: 22px;
    font-weight: 600;
    line-height: 1;
    color: var(--brand-green);
    letter-spacing: 0.2px;
  }
  .person-role {
    margin: 2px 0 0;
    font-size: 16.5px;
    line-height: 1.2;
    color: #333;
  }
  .contact-list {
    list-style: none;
    margin: 14px 0 0;
    padding: 0;
    font-size: 16.5px;
    line-height: 21px;
  }
  .contact-list li {
    display: flex;
    align-items: center;
    gap: 7px;
  }
  .contact-list svg {
    width: 15px;
    height: 15px;
    flex: none;
  }
  .web-accent {
    color: var(--brand-green);
  }
  .address {
    margin: 13px 0 0;
    font-size: 16.5px;
    line-height: 21px;
    font-style: normal;
  }
</style>
</head>
<body>

<section class="card card-front" aria-label="Business card front">
  <div class="wordmark">ZUB Capital</div>
  <div class="divider"></div>
  <div class="details">
    <h1 class="person-name">MARTIN KELLER</h1>
    <p class="person-role">Managing Director</p>
    <ul class="contact-list">
      <li>
        <svg viewBox="0 0 24 24" aria-hidden="true"><path fill="#314f22" d="M6.6 10.8a15.1 15.1 0 0 0 6.6 6.6l2.2-2.2c.3-.3.7-.4 1-.2 1.1.4 2.3.6 3.6.6.6 0 1 .4 1 1V20c0 .6-.4 1-1 1A17 17 0 0 1 3 4c0-.6.4-1 1-1h3.5c.6 0 1 .4 1 1 0 1.3.2 2.5.6 3.6.1.3 0 .7-.2 1z"/><path fill="none" stroke="#314f22" stroke-width="1.8" d="M14 3a7 7 0 0 1 7 7M14 7a3 3 0 0 1 3 3"/></svg>
        <span>044-123 456 789</span>
      </li>
      <li>
        <svg viewBox="0 0 24 24" aria-hidden="true"><rect x="1" y="5" width="22" height="14" fill="#314f22"/><path d="M1 5l11 8 11-8M1 19l8-7M23 19l-8-7" fill="none" stroke="#fff" stroke-width="1.5"/></svg>
        <span>info@webname.com</span>
      </li>
      <li>
        <svg viewBox="0 0 24 24" aria-hidden="true"><g fill="none" stroke="#314f22" stroke-width="1.8"><circle cx="12" cy="12" r="10"/><ellipse cx="12" cy="12" rx="4.5" ry="10"/><path d="M2 12h20M4 7h16M4 17h16"/></g></svg>
        <span>www.<span class="web-accent">websitename</span>.com</span>
      </li>
    </ul>
    <address class="address">421, Address line goes here<br>45452,Country Name</address>
  </div>
</section>

<section class="card card-back" aria-label="Business card back">
  <div class="wordmark">ZUB Capital</div>
</section>

</body>
</html>
```